Business card design Needed for new logo / Construction business, home extensions and new builds

We need a business card design using our new logo files which i will attach to this project :)

We are a small construction business specialising in home extensions, new builds and property development. We are very ambitious and would appreciate professional and elegant designs for our new business card.

Very serious about using the services on MakerQuarry and recently acquired our new logo from here :)

Please get involved, i will feedback when i can as i am very busy but can respond daily, thanks

Target Market(s)

People that want to build onto their houses, new building developments or adding too their existing property

Industry/Entity Type

Construction

Contact Information for Business Card

Renwick Tolliver Construction, Lionel Ashby (Managing Director), Tel 07822254961, email - info@renwick-tolliver, www.renwick-tolliver.co.uk

Colors

Designer to choose colors to be used in the design.

Requirements
Must have
• I like a deep grey on the back please. A lot of you have provided black from and back, try mixing things up a little. The black looks cool 😎 Thanks

```html
<!DOCTYPE html>
<html lang="en">
<head>
<meta charset="utf-8">
<title>Renwick Tolliver Construction – Business Card</title>
<link rel="stylesheet" href="https://fonts.googleapis.com/css2?family=Lato:wght@400;700;900&display=swap">
<style>
  :root {
    --canvas: #3a3a3c;
    --card-dark: #1d1d1e;
    --gold-deep: #b87d12;
    --gold-mid: #e0a52a;
    --gold-light: #fcd788;
    --silver-light: #e4e6e8;
    --silver-dark: #8f9499;
    --ink: #1a1a1a;
    --text-light: #e9e9e9;
    --text-muted: #b9b9b9;
  }
  * { box-sizing: border-box; margin: 0; padding: 0; }
  html, body { width: 1200px; height: 982px; overflow: hidden; }
  body {
    background: var(--canvas);
    font-family: "Lato", sans-serif;
    position: relative;
  }
  .card {
    position: absolute;
    width: 640px;
    height: 366px;
    border-radius: 22px;
    overflow: hidden;
  }
  /* Front */
  .card-front {
    left: 440px; top: 60px;
    background: linear-gradient(170deg, var(--gold-deep) 0%, var(--gold-mid) 18%, var(--gold-light) 40%, var(--gold-mid) 62%, var(--gold-deep) 78%, var(--gold-mid) 100%);
    display: flex; align-items: center; justify-content: center;
  }
  .front-mark {
    display: flex; flex-direction: column; align-items: center; gap: 18px;
  }
  .front-mark .square {
    width: 46px; height: 46px; background: var(--ink);
  }
  .front-mark .brand-name {
    font-weight: 700; font-size: 30px; letter-spacing: 2px;
    color: var(--ink); text-transform: uppercase; text-align: center; line-height: 1.25;
  }
  /* Back */
  .card-back {
    left: 140px; top: 520px;
    background: var(--card-dark);
  }
  .back-brand {
    position: absolute; left: 30px; top: 92px; width: 300px;
    display: flex; flex-direction: column; align-items: center; gap: 16px;
  }
  .back-brand .square { width: 38px; height: 38px; background: var(--gold-mid); }
  .back-brand .brand-name {
    font-weight: 700; font-size: 22px; letter-spacing: 1.5px;
    color: var(--gold-mid); text-transform: uppercase; text-align: center; line-height: 1.3;
  }
  .divider {
    position: absolute; left: 348px; top: 48px; width: 2px; height: 232px;
    background: var(--gold-mid);
  }
  .contact {
    position: absolute; left: 378px; top: 48px;
  }
  .contact .person {
    font-weight: 900; font-size: 28px; color: var(--gold-mid); text-transform: uppercase; letter-spacing: .5px;
  }
  .contact .role { font-size: 17px; color: var(--text-muted); margin-bottom: 14px; }
  .contact ul { list-style: none; }
  .contact li {
    display: flex; align-items: flex-start; gap: 10px;
    font-size: 15px; color: var(--text-light); line-height: 1.35; margin-bottom: 6px;
  }
  .contact svg { width: 15px; height: 15px; flex: none; margin-top: 2px; fill: var(--gold-mid); }
  .web-band { position: absolute; left: 0; bottom: 0; width: 640px; height: 62px; }
  .web-band .url {
    position: absolute; left: 70px; bottom: 18px;
    font-size: 15px; letter-spacing: 2px; color: var(--ink); font-weight: 700; text-transform: uppercase;
  }
</style>
</head>
<body>

<section class="card card-front" aria-label="Card front">
  <div class="front-mark">
    <div class="square"></div>
    <div class="brand-name">Renwick Tolliver<br>Construction</div>
  </div>
</section>

<section class="card card-back" aria-label="Card back">
  <div class="back-brand">
    <div class="square"></div>
    <div class="brand-name">Renwick Tolliver<br>Construction</div>
  </div>

  <div class="divider"></div>

  <div class="contact">
    <div class="person">Owen Hartley</div>
    <div class="role">Founder &amp; CEO</div>
    <ul>
      <li><svg viewBox="0 0 24 24"><path d="M12 2a7 7 0 0 0-7 7c0 5 7 13 7 13s7-8 7-13a7 7 0 0 0-7-7zm0 9.5A2.5 2.5 0 1 1 12 6.5a2.5 2.5 0 0 1 0 5z"/></svg><span>Your Address, City<br>State, Zip 1235</span></li>
      <li><svg viewBox="0 0 24 24"><path d="M6.6 10.8a15 15 0 0 0 6.6 6.6l2.2-2.2a1 1 0 0 1 1-.25 11.4 11.4 0 0 0 3.6.57 1 1 0 0 1 1 1V20a1 1 0 0 1-1 1A17 17 0 0 1 3 4a1 1 0 0 1 1-1h3.5a1 1 0 0 1 1 1c0 1.25.2 2.45.57 3.57a1 1 0 0 1-.25 1z"/></svg><span>(123) 456-7890</span></li>
      <li><svg viewBox="0 0 24 24"><path d="M7 1h10a2 2 0 0 1 2 2v18a2 2 0 0 1-2 2H7a2 2 0 0 1-2-2V3a2 2 0 0 1 2-2zm0 3v14h10V4z"/></svg><span>(231) 456-7890</span></li>
      <li><svg viewBox="0 0 24 24"><path d="M6 2h12v6H6zM4 9h16a2 2 0 0 1 2 2v6h-4v5H6v-5H2v-6a2 2 0 0 1 2-2zm4 7v4h8v-4z"/></svg><span>(312) 456-7890</span></li>
      <li><svg viewBox="0 0 24 24"><path d="M2 5h20v14H2zm2 2v.5l8 5 8-5V7z"/></svg><span>office@yourwebsite.com</span></li>
    </ul>
  </div>

  <svg class="web-band" viewBox="0 0 640 62" aria-hidden="true">
    <defs>
      <linearGradient id="band-gold" x1="0" y1="0" x2="1" y2="0">
        <stop offset="0" stop-color="#b87d12"/>
        <stop offset=".45" stop-color="#fcd788"/>
        <stop offset="1" stop-color="#c88a18"/>
      </linearGradient>
      <linearGradient id="band-silver" x1="0" y1="0" x2="1" y2="0">
        <stop offset="0" stop-color="#e4e6e8"/>
        <stop offset="1" stop-color="#8f9499"/>
      </linearGradient>
    </defs>
    <polygon points="0,0 540,0 505,62 0,62" fill="url(#band-gold)"/>
    <polygon points="555,0 640,0 640,62 520,62" fill="url(#band-silver)"/>
  </svg>
  <div class="web-band" style="pointer-events:none"><span class="url">www.renwicktolliverconstruction.com</span></div>
</section>

</body>
</html>
```